Business Cards Needed for Innovative Healthcare Marketing Company

We are a marketing company focused on healthcare. Our company is all about rebranding yourself renewing your image and generating results. The phoenix stands for "reborn" or "rising" which we provide new brands for our clients we take their old brands and renew it with creativity and innovation. I am looking for a business card with color dimension. I have attached an example of a card I think has the look and feel of what I am trying to accomplish. I like that the card example has black and grey font colors, I like the font placement and the small logo, I really like the use of the colors on the right those are the colors of my logo. My logo is phoenix so maybe incorporating flames similar to that design. I would like the back a solid color maybe red with an opaque version of the logo and website. As a marketing company I am always open to creative liberty!

Target Market(s)

Doctors and business professionals.

Industry/Entity Type

Marketing

Contact Information for Business Card

Valcorne Health Care Marketing
Marla Tenwick- CEO
#(512)638-2974
email-marla@valcorne.com
website- valcorne.com

Font styles to use
Sans Serif

Colors
ec1f27
f37122
ffc214
fbed22
fbf289
f04a50

Requirements
Must have
• The logo and required information
Nice to have
• icons by the information
Should not have
• child like font

```html
<!DOCTYPE html>
<html lang="en">
<head>
<meta charset="UTF-8">
<title>Valcorne Health Care Marketing — Business Card</title>
<link rel="stylesheet" href="https://fonts.googleapis.com/css2?family=Source+Sans+3:wght@300;400;600;700&display=swap">
<style>
  :root {
    --stage-bg: #ece9e6;
    --card-white: #ffffff;
    --brand-red: #9b1b22;
    --brand-orange: #f18a1f;
    --text-dark: #3a2a26;
    --back-orange: #f0901f;
    --back-red: #b3261e;
    --back-text: #ffffff;
  }
  * { margin: 0; padding: 0; box-sizing: border-box; }
  html, body {
    width: 1200px;
    height: 900px;
    overflow: hidden;
    background: var(--stage-bg);
    font-family: "Source Sans 3", Arial, sans-serif;
  }
  .canvas {
    position: relative;
    width: 1200px;
    height: 900px;
  }
  .card {
    position: absolute;
    box-shadow: 0 6px 18px rgba(0,0,0,0.18);
  }
  .card-front {
    left: 78px;
    top: 34px;
    width: 590px;
    height: 365px;
    background: var(--card-white);
  }
  .brand-mark {
    position: absolute;
    left: 48px;
    top: 42px;
    width: 78px;
    height: 78px;
    border-radius: 50%;
    background: var(--brand-red);
  }
  .brand-name {
    position: absolute;
    left: 137px;
    top: 40px;
    color: var(--brand-red);
    font-weight: 300;
    line-height: 1;
  }
  .brand-word {
    display: block;
    font-size: 56px;
    letter-spacing: 0.02em;
  }
  .brand-rule {
    display: block;
    width: 255px;
    height: 1px;
    margin: 6px 0 6px 0;
    background: var(--brand-red);
  }
  .brand-tagline {
    display: block;
    font-size: 21px;
    letter-spacing: 0.06em;
  }
  .person {
    position: absolute;
    left: 140px;
    top: 183px;
    width: 252px;
  }
  .person-name {
    font-size: 23px;
    font-weight: 700;
    color: var(--brand-red);
    line-height: 1.1;
  }
  .person-title {
    font-size: 16px;
    font-weight: 400;
    color: var(--brand-orange);
    margin-top: 4px;
    padding-bottom: 8px;
    border-bottom: 1px solid var(--brand-red);
  }
  .contact-list {
    list-style: none;
    margin-top: 12px;
  }
  .contact-item {
    display: flex;
    align-items: center;
    gap: 7px;
    font-size: 16px;
    color: var(--text-dark);
    height: 25px;
  }
  .contact-icon {
    width: 12px;
    height: 12px;
    flex: none;
    fill: var(--brand-orange);
  }
  .card-back {
    left: 388px;
    top: 505px;
    width: 566px;
    height: 352px;
    background: linear-gradient(225deg, var(--back-red) 0%, #c9451c 45%, var(--back-orange) 100%);
  }
  .back-website {
    position: absolute;
    right: 64px;
    top: 282px;
    color: var(--back-text);
    font-size: 16px;
    font-weight: 600;
    letter-spacing: 0.42em;
  }
</style>
</head>
<body>
<main class="canvas">
  <section class="card card-front" aria-label="Business card front">
    <div class="brand-mark" aria-hidden="true"></div>
    <div class="brand-name">
      <span class="brand-word">VALCORNE</span>
      <span class="brand-rule"></span>
      <span class="brand-tagline">HEALTHCARE MARKETING</span>
    </div>
    <div class="person">
      <h1 class="person-name">Marla Tenwick</h1>
      <p class="person-title">CEO</p>
      <ul class="contact-list">
        <li class="contact-item">
          <svg class="contact-icon" viewBox="0 0 24 24" aria-hidden="true"><path d="M6.6 10.8a15.1 15.1 0 0 0 6.6 6.6l2.2-2.2a1 1 0 0 1 1-.25 11.4 11.4 0 0 0 3.6.57 1 1 0 0 1 1 1V20a1 1 0 0 1-1 1A17 17 0 0 1 3 4a1 1 0 0 1 1-1h3.5a1 1 0 0 1 1 1c0 1.25.2 2.45.57 3.57a1 1 0 0 1-.25 1z"/></svg>
          (512)638-2974
        </li>
        <li class="contact-item">
          <svg class="contact-icon" viewBox="0 0 24 24" aria-hidden="true"><path d="M2 5h20v14H2z M2 5l10 8 10-8" fill="var(--brand-orange)"/><path d="M2 5l10 8 10-8" fill="none" stroke="#fff" stroke-width="1.6"/></svg>
          marla@valcorne.com
        </li>
        <li class="contact-item">
          <svg class="contact-icon" viewBox="0 0 24 24" aria-hidden="true"><circle cx="12" cy="12" r="10"/><path d="M2 12h20M12 2c3 3 3 17 0 20M12 2c-3 3-3 17 0 20" fill="none" stroke="#fff" stroke-width="1.4"/></svg>
          www.valcorne.com
        </li>
      </ul>
    </div>
  </section>

  <section class="card card-back" aria-label="Business card back">
    <p class="back-website">www.valcorne.com</p>
  </section>
</main>
</body>
</html>
```